Design a New Business Card for Our Company

We are looking for fresh, unique, and a modern business card that reflects our roots as digital marketing agency focused on SEM.

Industry/Entity Type

Marketing

Contact Information for Business Card

looking for very unique out of the box designs. clean and modern that compliments our logo

Requirements
Must have
• colors should match our logo
• Front should have name, address, email, and phone/fax of the person, phone/fax are the same number
• back should have our url

```html
<!DOCTYPE html>
<html lang="en">
<head>
<meta charset="utf-8">
<title>Brindlemoor Solutions – Business Card</title>
<link href="https://fonts.googleapis.com/css2?family=Arimo:wght@400;700&display=swap" rel="stylesheet">
<style>
  :root {
    --backdrop: #3b3431;
    --card: #1c1c1e;
    --card-edge: #2a2a2c;
    --text-light: #e6e6e6;
    --text-mid: #b9b9bb;
    --accent-blue: #4a8fd6;
    --rule: #8a8a8c;
  }
  * { box-sizing: border-box; margin: 0; padding: 0; }
  html, body {
    width: 1200px;
    height: 787px;
    overflow: hidden;
    background: var(--backdrop);
    font-family: "Arimo", Arial, sans-serif;
  }
  .stage {
    position: relative;
    width: 1200px;
    height: 787px;
  }
  .card {
    position: absolute;
    width: 540px;
    height: 308px;
    background: var(--card);
    border: 1px solid var(--card-edge);
    border-radius: 4px;
    box-shadow: 0 10px 30px rgba(0,0,0,0.35);
  }
  /* Back of card */
  .card-back {
    left: 50px;
    top: 90px;
  }
  .card-back .brand-mark {
    position: absolute;
    left: 0;
    right: 0;
    top: 96px;
    display: flex;
    justify-content: center;
    align-items: center;
    gap: 12px;
  }
  .brand-dot {
    width: 20px;
    height: 20px;
    border-radius: 50%;
    background: var(--accent-blue);
    flex: none;
  }
  .brand-name {
    font-weight: 700;
    font-size: 34px;
    color: var(--accent-blue);
    letter-spacing: 0.5px;
    white-space: nowrap;
  }
  .card-back .website {
    position: absolute;
    left: 0;
    right: 0;
    bottom: 70px;
    text-align: center;
    color: var(--text-light);
    font-size: 15px;
    letter-spacing: 6px;
  }
  /* Front of card */
  .card-front {
    left: 610px;
    top: 390px;
  }
  .card-front .brand-mark {
    position: absolute;
    left: 34px;
    top: 134px;
    display: flex;
    align-items: center;
    gap: 10px;
  }
  .card-front .brand-name { font-size: 28px; }
  .card-front .brand-dot { width: 16px; height: 16px; }
  .divider {
    position: absolute;
    left: 300px;
    top: 40px;
    width: 1px;
    height: 228px;
    background: linear-gradient(to bottom, transparent, var(--rule) 20%, var(--rule) 80%, transparent);
  }
  .contact {
    position: absolute;
    left: 322px;
    top: 54px;
    color: var(--text-light);
  }
  .contact .person-name {
    font-weight: 700;
    font-size: 20px;
    color: var(--text-mid);
  }
  .contact .person-title {
    font-size: 15px;
    color: var(--accent-blue);
    margin-bottom: 10px;
  }
  .contact .address {
    font-size: 15px;
    line-height: 1.35;
    margin-bottom: 6px;
  }
  .contact-line {
    display: flex;
    align-items: center;
    gap: 9px;
    font-size: 15px;
    line-height: 1.6;
  }
  .contact-line svg {
    width: 14px;
    height: 14px;
    fill: var(--text-mid);
    flex: none;
  }
</style>
</head>
<body>
<div class="stage">

  <section class="card card-back" aria-label="Card back">
    <div class="brand-mark">
      <span class="brand-dot"></span>
      <span class="brand-name">brindlemoor</span>
    </div>
    <p class="website">www.brindlemoor.com</p>
  </section>

  <section class="card card-front" aria-label="Card front">
    <div class="brand-mark">
      <span class="brand-dot"></span>
      <span class="brand-name">brindlemoor</span>
    </div>
    <div class="divider"></div>
    <div class="contact">
      <p class="person-name">Daniel Hart</p>
      <p class="person-title">President</p>
      <p class="address">2417 Linden Avenue<br>Maple Grove, NY 10020</p>
      <p class="contact-line">
        <svg viewBox="0 0 16 16" aria-hidden="true"><path d="M2 5c0-2 2-3 6-3s6 1 6 3v1h-3V4.5H5V6H2zM4 7h8l2 7H2z"/></svg>
        555 0142 7781
      </p>
      <p class="contact-line">
        <svg viewBox="0 0 16 16" aria-hidden="true"><path d="M4 1h7v4H4zM2 6h12v8H2zM4 9h4v1H4zm0 2h4v1H4zm6-2h2v3h-2z"/></svg>
        555 0198 3364
      </p>
      <p class="contact-line">
        <svg viewBox="0 0 16 16" aria-hidden="true"><path d="M1 3h14v10H1zm1 1v.5l6 4 6-4V4z"/></svg>
        dan@brindlemoor.com
      </p>
    </div>
  </section>

</div>
</body>
</html>
```